Website Design for a holiday home letting busines

We require a redesign of our present website www.pinebrookstays.com. We want the website to stand out and look professional and clean to make holiday hunters want to book a caravan or lodge holiday with us. Our logo is red however we DO NOT want the website to be red. We want a natural colour scheme.

The final design should communicate that we are a professional company to book with.

On the home page we require;
Overview of company
Photo
Search box for holiday (check in)
Late Deals
Reviews
News

We would like the following pages designed; home page, available dates page, caravans page, content page.

The website should be responsive for smart phones. One website I do like is http://www.verdoliso.be/nl/

Target Market(s)

Families

Industry/Entity Type

Travel

Number of Pages Required

5+ page

Font styles to use
Serif

Requirements
Must have
• The project must be responsive for mobile phones and tablets.
• Ability to search for holiday home holidays
• We want a natural colour scheme.
Nice to have
• A style we like is http://www.verdoliso.be/nl/
Should not have
• Do not use red as a colour for the website. Our logo is red so this is the only time we want this used.

```html
<!DOCTYPE html>
<html lang="en">
<head>
<meta charset="utf-8">
<title>Pinebrook Stays – Private Holiday Homes</title>
<link href="https://fonts.googleapis.com/css2?family=Open+Sans:wght@400;600;700&display=swap" rel="stylesheet">
<style>
:root{
  --teal:#2b9fb0;
  --teal-dark:#1f7c8a;
  --ink:#333a3f;
  --muted:#7a8288;
  --line:#e2e5e7;
  --nav:#3b4146;
  --topbar:#1d5e69;
  --page:#ffffff;
  --soft:#f4f5f6;
  --footer:#2a2e31;
  --footer-low:#222527;
  --shade:rgba(0,0,0,.64);
}
*{box-sizing:border-box;margin:0;padding:0}
html,body{width:1200px;height:3040px;overflow:hidden}
body{font-family:"Open Sans",Arial,sans-serif;color:var(--ink);background:var(--page);position:relative;font-size:14px}
.site{position:absolute;inset:0}
.topbar{height:12px;background:var(--topbar)}
.header{height:116px;position:relative;padding:0 72px}
.brand{position:absolute;left:72px;top:30px;display:flex;align-items:center;gap:12px}
.brand-dot{width:52px;height:52px;border-radius:50%;background:#b8322e}
.brand-name{font-size:26px;font-weight:700;color:var(--ink)}
.social{position:absolute;right:72px;top:30px;display:flex;gap:8px}
.social span{width:22px;height:22px;border-radius:50%;background:#c9cdd0}
.contact{position:absolute;right:72px;top:80px;display:flex;gap:28px;font-size:13px;color:var(--muted)}
.nav{height:40px;background:var(--nav);display:flex;padding:0 72px}
.nav a{color:#dfe3e5;text-decoration:none;font-size:13px;line-height:40px;padding:0 22px;text-transform:uppercase}
.nav a.active{background:var(--teal);color:#fff}
.hero{position:relative;height:592px;background:linear-gradient(180deg,#9cc4dc 0%,#c7dcc0 55%,#6f9a3c 78%,#4f7a2a 100%)}
.hero-title{position:absolute;left:72px;top:160px;color:#fff;font-size:38px;font-weight:700;letter-spacing:1px}
.hero-sub{position:absolute;left:72px;top:212px;color:#fff;font-size:16px;width:420px;line-height:24px}
.search{position:absolute;left:72px;top:292px;width:428px;height:160px;background:rgba(255,255,255,.92);padding:18px}
.search label{font-size:12px;color:var(--muted);display:block;margin-bottom:4px}
.search .row{display:flex;gap:12px;margin-bottom:14px}
.search .field{flex:1}
.search .box{height:32px;border:1px solid var(--line);background:#fff}
.search .go{position:absolute;right:18px;bottom:16px;width:120px;height:34px;background:var(--teal);color:#fff;font-size:13px;text-align:center;line-height:34px}
.hero-circle{position:absolute;left:580px;top:72px;width:420px;height:420px;border-radius:50%;background:linear-gradient(135deg,#e9e4dc,#b9a58c);border:10px solid #fff}
.hero-dots{position:absolute;left:72px;bottom:24px;display:flex;gap:10px}
.hero-dots span{width:28px;height:28px;background:rgba(255,255,255,.7)}
.section-title{text-align:center;font-size:30px;font-weight:600;letter-spacing:2px;text-transform:uppercase}
.rule{width:80px;height:3px;background:var(--teal);margin:10px auto 0}
.overview{height:300px;padding-top:76px;text-align:center}
.overview p{width:1000px;margin:30px auto 0;font-size:13px;line-height:21px;color:var(--muted)}
.btn{display:inline-block;background:var(--teal);color:#fff;font-size:13px;padding:0 22px;line-height:34px;text-transform:uppercase}
.overview .btn{margin-top:22px}
.deals{height:420px;background:linear-gradient(180deg,#6b4a35,#8a6244 60%,#5a3d2a);padding-top:60px;position:relative}
.deals .section-title{color:#fff}
.deal-row{display:flex;gap:40px;padding:0 80px;margin-top:40px}
.deal{flex:1;background:#fff;height:220px;position:relative}
.deal-photo{height:140px;margin:8px;background:linear-gradient(135deg,#d8d2c8,#9d8d78)}
.deal-badge{position:absolute;right:14px;top:14px;width:60px;height:60px;border-radius:50%;background:var(--teal);color:#fff;font-size:11px;text-align:center;padding-top:14px;line-height:15px;font-weight:600}
.deal h4{font-size:13px;margin:6px 14px 2px}
.deal p{font-size:11px;color:var(--muted);margin:0 14px}
.deal-dots{position:absolute;left:0;right:0;bottom:14px;display:flex;justify-content:center;gap:8px}
.deal-dots span{width:14px;height:14px;border-radius:50%;background:#d9d9d9}
.caravans{height:700px;padding-top:92px}
.caravan-grid{display:grid;grid-template-columns:1fr 1fr;gap:60px 72px;padding:0 80px;margin-top:56px}
.caravan{display:flex;gap:20px;height:160px}
.caravan-photo{width:190px;height:160px;background:linear-gradient(135deg,#cfc6b8,#7f6e5a)}
.caravan h4{font-size:16px;margin-bottom:10px;text-transform:uppercase}
.caravan dl{display:grid;grid-template-columns:auto auto;gap:4px 28px;font-size:12px;color:var(--muted)}
.caravan .btn{margin-top:16px;font-size:11px;line-height:28px;padding:0 16px}
.feeds{height:460px;display:flex;gap:60px;padding:12px 72px 0}
.feed{flex:1}
.feed h3{font-size:22px;font-weight:600;text-transform:uppercase;letter-spacing:1px;margin-bottom:28px}
.review{margin-bottom:24px;font-size:12px;color:var(--muted);line-height:19px}
.review .date{color:var(--teal)}
.review strong{display:block;color:var(--ink)}
.item{display:flex;gap:14px;margin-bottom:22px;font-size:12px;color:var(--muted);line-height:19px}
.item .sq{flex:none;width:26px;height:26px;background:#4a6ea8}
.item .av{flex:none;width:52px;height:52px;border-radius:50%;background:#c9bfb1}
.item b{color:var(--teal);display:block;font-weight:600}
.footer{height:400px;background:var(--footer);position:relative;padding:54px 72px 0;color:#c3c8cc}
.footer h5{font-size:14px;text-transform:uppercase;letter-spacing:1px;color:#fff;margin-bottom:20px}
.links{display:flex;gap:60px;width:700px}
.links ul{list-style:none;font-size:12px;line-height:26px}
.links li::before{content:"›";color:var(--teal);margin-right:8px}
.news{position:absolute;left:880px;top:54px;width:248px}
.news .in{display:flex}
.news .in span{flex:1;height:30px;background:#fff}
.news .in b{width:32px;height:30px;background:var(--teal)}
.pay{margin-top:40px}
.pay .cards{display:flex;gap:8px}
.pay .cards span{width:34px;height:22px;background:#d5d8db;border-radius:2px}
.copy{position:absolute;left:0;right:0;bottom:0;height:110px;background:var(--footer-low);padding:32px 72px;font-size:11px;color:#8d9398;line-height:19px}
.shade{position:absolute;inset:0;background:var(--shade)}
.popup{position:absolute;left:360px;top:112px;width:512px;height:368px;background:#fff;border:6px solid #fff;box-shadow:0 0 12px rgba(0,0,0,.5)}
.ad{width:100%;height:100%;background:linear-gradient(160deg,#d6e6f1 0%,#9fb9cc 100%);position:relative;overflow:hidden}
.ad h2{text-align:center;font-size:38px;font-weight:600;color:#111;line-height:44px;padding-top:26px;letter-spacing:-.5px}
.ad-visual{position:absolute;left:0;right:0;bottom:0;height:230px;background:linear-gradient(180deg,rgba(255,255,255,0) 0%,#8aa6bb 100%)}
.close{position:absolute;right:-20px;top:-20px;width:36px;height:36px;border-radius:50%;background:#fff;border:3px solid #222;display:flex;align-items:center;justify-content:center}
</style>
</head>
<body>
<div class="site">
  <div class="topbar"></div>
  <header class="header">
    <div class="brand"><span class="brand-dot"></span><span class="brand-name">Pinebrook Stays</span></div>
    <div class="social"><span></span><span></span><span></span><span></span><span></span></div>
    <div class="contact"><span>☎ +44 1632 960 418</span><span>✉ hello@pinebrookstays.com</span></div>
  </header>
  <nav class="nav">
    <a class="active">Home</a><a>About Us</a><a>Caravans</a><a>Lodges</a><a>Available Dates</a><a>Late Deals</a><a>Reviews</a><a>News</a><a>Contact Us</a>
  </nav>
  <section class="hero" role="img" aria-label="Holiday park photograph with green lawn and sky">
    <h1 class="hero-title">PRIVATE HOLIDAY HOMES</h1>
    <p class="hero-sub">Quality lodges &amp; caravans for hire in a peaceful park setting close to the coast.</p>
    <form class="search">
      <div class="row">
        <div class="field"><label>Check in</label><div class="box"></div></div>
        <div class="field"><label>Nights</label><div class="box"></div></div>
      </div>
      <div class="row"><div class="field"><label>Guests</label><div class="box" style="width:60%"></div></div></div>
      <span class="go">Search</span>
    </form>
    <div class="hero-circle" role="img" aria-label="Lodge interior photograph"></div>
    <div class="hero-dots"><span></span><span></span></div>
  </section>
  <section class="overview">
    <h2 class="section-title">Overview of Company</h2>
    <div class="rule"></div>
    <p>Pinebrook Stays is a family run business offering privately owned caravans and lodges on a beautiful holiday park. Every home is cleaned and checked before you arrive, with fresh linen, a fitted kitchen and outdoor decking. Whether you want a short break or a full summer week, our friendly team is here to help you find the right home and make booking simple from start to finish.</p>
    <span class="btn">Read More</span>
  </section>
  <section class="deals" role="img" aria-label="Warm toned lounge photograph behind late deals">
    <h2 class="section-title">Late Deals</h2>
    <div class="deal-row">
      <div class="deal"><div class="deal-photo" role="img" aria-label="Caravan lounge photograph"></div><span class="deal-badge">SAVE<br>20%</span><h4>THE FLORIDA</h4><p>FRIDAY 09 SEPTEMBER 2016 (3 NIGHTS)</p></div>
      <div class="deal"><div class="deal-photo" role="img" aria-label="Caravan lounge photograph"></div><span class="deal-badge">SAVE<br>20%</span><h4>THE FLORIDA</h4><p>FRIDAY 09 SEPTEMBER 2016 (3 NIGHTS)</p></div>
      <div class="deal"><div class="deal-photo" role="img" aria-label="Caravan lounge photograph"></div><span class="deal-badge">SAVE<br>20%</span><h4>THE FLORIDA</h4><p>FRIDAY 09 SEPTEMBER 2016 (3 NIGHTS)</p></div>
    </div>
    <div class="deal-dots"><span></span><span></span></div>
  </section>
  <section class="caravans">
    <h2 class="section-title">List of Caravans &amp; Lodges</h2>
    <div class="rule"></div>
    <div class="caravan-grid">
      <div class="caravan"><div class="caravan-photo" role="img" aria-label="Caravan interior photograph"></div><div><h4>The Burgundy</h4><dl><dt>Sleeps</dt><dd>6 Guests</dd><dt>Bedrooms</dt><dd>3</dd><dt>Heating</dt><dd>Central</dd></dl><span class="btn">View Details</span></div></div>
      <div class="caravan"><div class="caravan-photo" role="img" aria-label="Caravan interior photograph"></div><div><h4>The Burgundy</h4><dl><dt>Sleeps</dt><dd>6 Guests</dd><dt>Bedrooms</dt><dd>3</dd><dt>Heating</dt><dd>Central</dd></dl><span class="btn">View Details</span></div></div>
      <div class="caravan"><div class="caravan-photo" role="img" aria-label="Caravan interior photograph"></div><div><h4>The Burgundy</h4><dl><dt>Sleeps</dt><dd>6 Guests</dd><dt>Bedrooms</dt><dd>3</dd><dt>Heating</dt><dd>Central</dd></dl><span class="btn">View Details</span></div></div>
      <div class="caravan"><div class="caravan-photo" role="img" aria-label="Caravan interior photograph"></div><div><h4>The Burgundy</h4><dl><dt>Sleeps</dt><dd>6 Guests</dd><dt>Bedrooms</dt><dd>3</dd><dt>Heating</dt><dd>Central</dd></dl><span class="btn">View Details</span></div></div>
    </div>
  </section>
  <section class="feeds">
    <div class="feed"><h3>Latest Reviews</h3>
      <div class="review"><span class="date">12 August 2016</span><strong>Stayed in The Burgundy</strong>Lovely clean caravan with everything we needed. The kids loved the park and we will be back next year. Read more</div>
      <div class="review"><span class="date">03 August 2016</span><strong>Stayed in The Florida</strong>Friendly owners and a spotless home. Great base for days out along the coast. Read more</div>
    </div>
    <div class="feed"><h3>Community Feed</h3>
      <div class="item"><span class="sq"></span><div><b>Pinebrook Stays</b>New late deals added for September. Book early to avoid missing out on a break.</div></div>
      <div class="item"><span class="sq"></span><div><b>Pinebrook Stays</b>Thank you to all our guests this summer for the kind words and photos.</div></div>
      <div class="item"><span class="sq"></span><div><b>Pinebrook Stays</b>The new lodge is now open for bookings from next spring onwards.</div></div>
    </div>
    <div class="feed"><h3>Blog Feed</h3>
      <div class="item"><span class="av" role="img" aria-label="Author photo"></span><div><b>Park News</b>Our guide to the best family walks near the park this autumn. Read more</div></div>
      <div class="item"><span class="av" role="img" aria-label="Author photo"></span><div><b>Park News</b>Five easy tips for packing light on your caravan holiday. Read more</div></div>
    </div>
  </section>
  <footer class="footer">
    <h5>Useful Links</h5>
    <div class="links">
      <ul><li>Home</li><li>About Us</li><li>Caravans</li><li>Lodges</li><li>Late Deals</li></ul>
      <ul><li>Available Dates</li><li>Reviews</li><li>News</li><li>Gallery</li><li>Contact Us</li></ul>
      <ul><li>Terms &amp; Conditions</li><li>Privacy Policy</li><li>Park Rules</li><li>FAQs</li><li>Sitemap</li></ul>
    </div>
    <div class="news"><h5>Newsletter</h5><div class="in"><span></span><b></b></div>
      <div class="pay"><h5>Pay Through</h5><div class="cards"><span></span><span></span><span></span><span></span></div></div>
    </div>
    <div class="copy">© 2016 Pinebrook Stays. All rights reserved. www.pinebrookstays.com<br>Privately owned holiday homes for hire. Registered in England. Prices and availability subject to change.</div>
  </footer>
</div>
<div class="shade"></div>
<div class="popup">
  <div class="ad">
    <h2>Plan less,<br>stay longer.</h2>
    <div class="ad-visual" role="img" aria-label="Promotional product photograph"></div>
  </div>
  <span class="close"><svg width="14" height="14" viewBox="0 0 14 14"><path d="M2 2L12 12M12 2L2 12" stroke="#222" stroke-width="3"/></svg></span>
</div>
</body>
</html>
```